Business Card Design

We need a business card designed for our new company. Prefer a black card with white logo & writing.

Contact Information for Business Card

Ted Galloway, address: 7-4812 Fernhollow Road, Abbotsford, BC, V3K 8R2, Office Phone: 604-712-3390, Cell: 604-947-2164, Email: ted@resinworkshub.ca

Colors

Designer to choose only greyscale colors for use in the design.

```html
<!DOCTYPE html>
<html lang="en">
<head>
<meta charset="utf-8">
<title>Resinworks Hub — Business Card</title>
<link href="https://fonts.googleapis.com/css2?family=Montserrat:wght@400;500;700;800&display=swap" rel="stylesheet">
<style>
  :root {
    --backdrop: #1f1f1f;
    --card: #000000;
    --ink: #ffffff;
    --ink-soft: #e6e6e6;
  }
  * { margin: 0; padding: 0; box-sizing: border-box; }
  html, body {
    width: 1200px;
    height: 900px;
    overflow: hidden;
    background: var(--backdrop);
    font-family: "Montserrat", sans-serif;
    color: var(--ink);
  }
  .stage { position: relative; width: 1200px; height: 900px; }
  .card {
    position: absolute;
    left: 341px;
    width: 518px;
    height: 296px;
    background: var(--card);
    overflow: hidden;
  }
  .card--front { top: 141px; }
  .card--back { top: 463px; }

  .wordmark {
    position: absolute;
    display: flex;
    align-items: center;
    gap: 10px;
    font-weight: 800;
    color: var(--ink);
    letter-spacing: 0.5px;
    white-space: nowrap;
  }
  .wordmark__dot {
    border: 3px solid var(--ink);
    border-radius: 50%;
    flex: none;
  }
  .card--front .wordmark { left: 26px; top: 74px; font-size: 24px; }
  .card--front .wordmark__dot { width: 24px; height: 24px; }
  .card--back .wordmark {
    left: 50%;
    top: 50%;
    transform: translate(-50%, -50%);
    font-size: 36px;
    gap: 14px;
  }
  .card--back .wordmark__dot { width: 36px; height: 36px; border-width: 4px; }

  .divider { position: absolute; left: 0; top: 0; width: 518px; height: 296px; }

  .holder {
    position: absolute;
    right: 28px;
    top: 196px;
    font-size: 17px;
    font-weight: 700;
    letter-spacing: 0.3px;
    text-transform: uppercase;
  }
  .contact-list {
    position: absolute;
    left: 27px;
    top: 201px;
    list-style: none;
    font-size: 14px;
    line-height: 18px;
    color: var(--ink-soft);
  }
  .contact-list li { display: flex; align-items: center; gap: 5px; }
  .contact-list svg { width: 12px; height: 12px; flex: none; }
  .address {
    position: absolute;
    right: 28px;
    top: 236px;
    text-align: right;
    font-style: normal;
    font-size: 14px;
    line-height: 18px;
    color: var(--ink-soft);
  }
</style>
</head>
<body>
<main class="stage">
  <section class="card card--front">
    <div class="wordmark"><span class="wordmark__dot"></span><span>RESINWORKS HUB</span></div>

    <svg class="divider" viewBox="0 0 518 296" aria-hidden="true">
      <polyline points="0,188 292,188 358,225 518,225" fill="none" stroke="#ffffff" stroke-width="1.3"/>
    </svg>

    <p class="holder">Ted Galloway</p>

    <ul class="contact-list">
      <li>
        <svg viewBox="0 0 24 24" aria-hidden="true"><path fill="#ffffff" d="M6.6 10.8a15.1 15.1 0 0 0 6.6 6.6l2.2-2.2a1 1 0 0 1 1-.25 11.4 11.4 0 0 0 3.6.57 1 1 0 0 1 1 1V20a1 1 0 0 1-1 1A17 17 0 0 1 3 4a1 1 0 0 1 1-1h3.5a1 1 0 0 1 1 1c0 1.25.2 2.45.57 3.57a1 1 0 0 1-.25 1z"/></svg>
        <span>604-712-3390</span>
      </li>
      <li>
        <svg viewBox="0 0 24 24" aria-hidden="true"><rect x="6" y="2" width="12" height="20" rx="2" fill="none" stroke="#ffffff" stroke-width="2"/><circle cx="12" cy="18" r="1.2" fill="#ffffff"/></svg>
        <span>604-947-2164</span>
      </li>
      <li>
        <svg viewBox="0 0 24 24" aria-hidden="true"><path fill="#ffffff" d="M2 5h20v14H2z"/><path d="M2 5l10 8 10-8" fill="none" stroke="#000000" stroke-width="2"/></svg>
        <span>ted@resinworkshub.ca</span>
      </li>
      <li>
        <svg viewBox="0 0 24 24" aria-hidden="true"><g fill="none" stroke="#ffffff" stroke-width="1.8"><circle cx="12" cy="12" r="10"/><ellipse cx="12" cy="12" rx="4.5" ry="10"/><path d="M2 12h20M4 7h16M4 17h16"/></g></svg>
        <span>resinworkshub.ca</span>
      </li>
    </ul>

    <address class="address">
      7-4812 Fernhollow Road<br>
      Abbotsford, BC, V3K 8R2
    </address>
  </section>

  <section class="card card--back">
    <div class="wordmark"><span class="wordmark__dot"></span><span>RESINWORKS HUB</span></div>
  </section>
</main>
</body>
</html>
```